Quillmarsh Property Solutions need a business card design

Hello guys. We would need a business card design asap please.
We are a start up property investment business based in London UK specialised in buying, selling, managing and letting properties and helping distressed property owners.
The name of our Business is Quillmarsh, the logo symbolises the four fundamental elements of the world (earth, air, fire and water) and so it stands for strength, stability, longevity.
We would like the business card to communicate professionalism and reliability. Many many thanks indeed for your work.

Details:

1.) Rosalind Updike
Property Investor
Mobile: +44(0)7700123456
Email: rosalind.quillmarsh@mailbox-example.com

2.) Dominic Updike
Property Investor
Mobile: +44(0)7700987654
Email: dominic.quillmarsh@mailbox-example.com

```html
<!DOCTYPE html>
<html lang="en">
<head>
<meta charset="utf-8">
<title>Quillmarsh Property Solutions – Business Card</title>
<link href="https://fonts.googleapis.com/css2?family=Open+Sans:wght@400;700&display=swap" rel="stylesheet">
<style>
  :root {
    --backdrop: #e3e4e6;
    --card: #ffffff;
    --ink: #111111;
    --ink-soft: #9a9a9a;
    --band-red: #e0232b;
    --band-green: #1fa53d;
    --band-blue: #2a63c8;
    --card-shadow: 0 14px 28px rgba(0, 0, 0, 0.16), 0 2px 4px rgba(0, 0, 0, 0.08);
  }
  * { box-sizing: border-box; margin: 0; padding: 0; }
  html, body {
    width: 1200px;
    height: 800px;
    overflow: hidden;
    background: var(--backdrop);
    font-family: "Open Sans", Arial, sans-serif;
  }
  .canvas {
    position: relative;
    width: 1200px;
    height: 800px;
  }
  .card {
    position: absolute;
    width: 490px;
    height: 280px;
    background: var(--card);
    box-shadow: var(--card-shadow);
    overflow: hidden;
  }

  /* Front */
  .card--front { left: 80px; top: 320px; }
  .front-brand {
    position: absolute;
    left: 96px;
    top: 96px;
    display: flex;
    align-items: center;
    gap: 22px;
  }
  .brand-square {
    width: 44px;
    height: 44px;
    background: var(--ink-soft);
  }
  .front-brand .brand-name {
    color: var(--ink-soft);
    font-weight: 400;
    font-size: 21px;
    line-height: 1.15;
    letter-spacing: 1px;
    text-transform: uppercase;
  }
  .edge-band {
    position: absolute;
    left: 0;
    right: 0;
    bottom: 0;
    height: 16px;
    display: flex;
  }
  .edge-band span { flex: 1; }
  .edge-band .red { background: var(--band-red); }
  .edge-band .green { background: var(--band-green); }
  .edge-band .blue { background: var(--band-blue); }

  /* Back */
  .card--back { left: 630px; top: 180px; }
  .back-brand {
    position: absolute;
    left: 60px;
    top: 50px;
  }
  .back-brand .brand-square {
    width: 40px;
    height: 40px;
    background: var(--ink);
    margin-bottom: 12px;
  }
  .back-brand .brand-name {
    color: var(--ink);
    font-weight: 700;
    font-size: 13px;
    line-height: 1.2;
    letter-spacing: 0.5px;
    text-transform: uppercase;
  }
  .contact {
    position: absolute;
    left: 200px;
    right: 16px;
    top: 148px;
    color: var(--ink);
  }
  .contact .person-name {
    font-size: 17px;
    font-weight: 400;
    margin-bottom: 4px;
  }
  .contact p {
    font-size: 10.5px;
    line-height: 1.4;
    white-space: nowrap;
  }
</style>
</head>
<body>
<main class="canvas">

  <section class="card card--front" aria-label="Card front">
    <div class="front-brand">
      <div class="brand-square" aria-hidden="true"></div>
      <p class="brand-name">Quillmarsh<br>Property Solutions</p>
    </div>
    <div class="edge-band" aria-hidden="true">
      <span class="red"></span>
      <span class="green"></span>
      <span class="blue"></span>
      <span class="red"></span>
      <span class="green"></span>
    </div>
  </section>

  <section class="card card--back" aria-label="Card back">
    <div class="back-brand">
      <div class="brand-square" aria-hidden="true"></div>
      <p class="brand-name">Quillmarsh<br>Property Solutions</p>
    </div>
    <div class="contact">
      <h1 class="person-name">Rosalind Updike</h1>
      <p>Property Investor</p>
      <p>Mobile: +44(0)7700123456</p>
      <p>Email: rosalind.quillmarsh@mailbox-example.com</p>
    </div>
  </section>

</main>
</body>
</html>
```